Classy, Elegant, Simple Business Card Design

Looking to have a classy, simple, and elegant design. Want a top notch designed business card. I really like the look of the new torvane credit card. I also like the design I attached. I am trying to reach 21-29 year old females for booking us for there wedding or event. We offer Disc Jockey Service, Photo Booth Rentals, and Uplighting .

Target Market(s)

21-28 year old females

Contact Information for Business Card

Has to have logo, website, email, and phone number

Font styles to use
Other font styles liked:
• open to font choice, modern, clean
Designer to choose
33a6d7
0791cd
0555a3
ffffff

Requirements
Must have
• Has to have logo, website, email, and phone number
Nice to have
• I really like the design of the new torvane credit card. I also included my logo and some designs I like
Should not have
• clutter or too much info

```html
<!DOCTYPE html>
<html lang="en">
<head>
<meta charset="utf-8">
<title>Tidelight Event Group – Business Card</title>
<link rel="stylesheet" href="https://fonts.googleapis.com/css2?family=Questrial&family=Roboto:wght@400;500&display=swap">
<style>
  :root {
    --stage: #2a2a2b;
    --card: #1c1d1f;
    --card-edge: #2e3033;
    --silver: #c9ccd1;
    --silver-dim: #7d8187;
    --blue: #0791cd;
    --blue-light: #33a6d7;
    --blue-deep: #0555a3;
    --white: #ffffff;
  }
  * { margin: 0; padding: 0; box-sizing: border-box; }
  html, body { width: 799px; height: 1200px; overflow: hidden; }
  body {
    background: var(--stage);
    position: relative;
    font-family: "Roboto", Arial, sans-serif;
  }
  .card {
    position: absolute;
    left: 80px;
    width: 640px;
    height: 366px;
    background: var(--card);
    border: 1px solid var(--card-edge);
    overflow: hidden;
  }
  .card--front { top: 170px; }
  .card--back { top: 690px; }

  /* Front */
  .front-brand {
    position: absolute;
    inset: 0;
    display: flex;
    flex-direction: column;
    align-items: center;
    justify-content: center;
    gap: 10px;
  }
  .brand-name {
    font-family: "Questrial", sans-serif;
    color: var(--silver);
    font-size: 58px;
    letter-spacing: 3px;
    line-height: 1;
  }
  .brand-sub {
    font-family: "Questrial", sans-serif;
    color: var(--silver-dim);
    font-size: 20px;
    letter-spacing: 9px;
  }

  /* Back */
  .ornament {
    position: absolute;
    left: 10px;
    top: 23px;
    width: 320px;
    height: 320px;
    border-radius: 50%;
    background: radial-gradient(circle, transparent 0 58%, #5d6065 60%, #3a3c40 80%, transparent 100%);
  }
  .emblem {
    position: absolute;
    left: 50px;
    top: 63px;
    width: 240px;
    height: 240px;
    border-radius: 50%;
    border: 2px solid var(--silver);
    background: var(--card);
    display: flex;
    align-items: center;
    justify-content: center;
  }
  .emblem-name {
    font-family: "Questrial", sans-serif;
    color: var(--blue);
    font-size: 30px;
    letter-spacing: 2px;
  }
  .details {
    position: absolute;
    left: 372px;
    top: 96px;
    width: 250px;
  }
  .details .brand-name { font-size: 30px; letter-spacing: 1px; color: var(--white); }
  .details .brand-sub { font-size: 11px; letter-spacing: 5px; margin-top: 3px; }
  .person-name {
    margin-top: 22px;
    color: var(--blue);
    font-weight: 500;
    font-size: 22px;
  }
  .person-role { color: var(--white); font-size: 14px; margin-top: 2px; }
  .contact-list { list-style: none; margin-top: 18px; }
  .contact-list li {
    display: flex;
    align-items: center;
    gap: 12px;
    color: var(--white);
    font-size: 15px;
    height: 26px;
  }
  .contact-list svg { width: 14px; height: 14px; fill: var(--blue); flex: none; }
</style>
</head>
<body>
  <section class="card card--front">
    <div class="front-brand">
      <div class="brand-name">TIDELIGHT</div>
      <div class="brand-sub">EVENT GROUP</div>
    </div>
  </section>

  <section class="card card--back">
    <div class="ornament" role="img" aria-label="Silver radiating sound-bar ornament around the emblem"></div>
    <div class="emblem"><span class="emblem-name">TIDELIGHT</span></div>
    <div class="details">
      <div class="brand-name">TIDELIGHT</div>
      <div class="brand-sub">EVENT GROUP</div>
      <div class="person-name">Mara Ellison</div>
      <div class="person-role">Founder &amp; CEO</div>
      <ul class="contact-list">
        <li>
          <svg viewBox="0 0 16 16" aria-hidden="true"><path d="M3 1h3l1.5 4-2 1.2a9 9 0 0 0 4.3 4.3L11 8.5l4 1.5v3a2 2 0 0 1-2 2A12 12 0 0 1 1 3a2 2 0 0 1 2-2z"/></svg>
          555 0147 0182
        </li>
        <li>
          <svg viewBox="0 0 16 16" aria-hidden="true"><path d="M1 3h14v10H1z M1 3l7 6 7-6" fill="none" stroke="#0791cd" stroke-width="1.6"/></svg>
          mara@tidelight.com
        </li>
        <li>
          <svg viewBox="0 0 16 16" aria-hidden="true"><g fill="none" stroke="#0791cd" stroke-width="1.4"><circle cx="8" cy="8" r="6.5"/><ellipse cx="8" cy="8" rx="3" ry="6.5"/><path d="M1.5 8h13"/></g></svg>
          www.tidelight.com
        </li>
      </ul>
    </div>
  </section>
</body>
</html>
```